BildeVOLD buisnesscard

Hey :) I need a modern buisnesscard for my company BildeVOLD
It most have:
Dagligleder og Fotograf: Henrik Audun Strandvik

Mob: +4755526408
Epost: post@bildevold.example
Adresse: Kvernbakken9, 6040 Solvikvåg

Facbook and instagram logo with text BildeVOLD

BildeVOLD logo

It Company

```html
<!DOCTYPE html>
<html lang="no">
<head>
<meta charset="utf-8">
<title>BildeVOLD – visittkort</title>
<link href="https://fonts.googleapis.com/css2?family=Noto+Sans:wght@400;500&display=swap" rel="stylesheet">
<style>
  :root {
    --page: #e4e4e4;
    --card-dark: #252525;
    --brand-blue: #2f8fbd;
    --brand-pink: #d4579a;
    --pink-fold: #9e4677;
    --text-light: #ffffff;
    --mark-grey: #9b9b9b;
  }
  * { margin: 0; padding: 0; box-sizing: border-box; }
  html, body { width: 1200px; height: 1200px; overflow: hidden; }
  body {
    background: var(--page);
    font-family: "Noto Sans", Verdana, sans-serif;
    position: relative;
  }
  .card {
    position: absolute;
    width: 720px;
    height: 434px;
    background: var(--card-dark);
    overflow: hidden;
    box-shadow: 0 6px 16px rgba(0,0,0,0.25);
  }
  .card--front { left: 240px; top: 106px; }
  .card--back { left: 240px; top: 624px; }

  .card__shapes { position: absolute; inset: 0; }

  .brand-name {
    position: absolute;
    left: 182px;
    top: 172px;
    transform: translate(-50%, -50%);
    font-size: 46px;
    font-weight: 500;
    color: var(--brand-pink);
    letter-spacing: 0.5px;
    white-space: nowrap;
  }

  .holder-name {
    position: absolute;
    right: 28px;
    top: 104px;
    height: 59px;
    line-height: 59px;
    font-size: 27px;
    color: var(--text-light);
    white-space: nowrap;
  }
  .holder-role {
    position: absolute;
    right: 30px;
    top: 170px;
    font-size: 16.5px;
    color: var(--text-light);
    letter-spacing: 0.3px;
  }

  .contact-list { list-style: none; }
  .contact-item {
    position: absolute;
    right: 30px;
    height: 30px;
    display: flex;
    align-items: center;
    gap: 16px;
    font-size: 19px;
    color: var(--text-light);
    letter-spacing: 0.4px;
    white-space: nowrap;
    transform: translateY(-50%);
  }
  .contact-item svg { width: 29px; height: 29px; flex: none; }

  .back-brand {
    position: absolute;
    left: 50%;
    top: 212px;
    transform: translate(-50%, -50%);
    font-size: 70px;
    font-weight: 500;
    color: var(--mark-grey);
    white-space: nowrap;
  }
  .social-row {
    position: absolute;
    left: 0; right: 0;
    top: 334px;
    display: flex;
    justify-content: center;
    gap: 22px;
    color: var(--mark-grey);
    font-size: 19.5px;
  }
  .social-item { display: flex; align-items: center; gap: 12px; }
  .social-dot {
    width: 33px; height: 33px;
    border: 2px solid var(--mark-grey);
    border-radius: 50%;
  }
</style>
</head>
<body>

<section class="card card--front" aria-label="Visittkort forside">
  <svg class="card__shapes" viewBox="0 0 720 434" aria-hidden="true">
    <polygon points="512,0 720,0 720,434 290,434" fill="var(--brand-blue)"/>
    <polygon points="374,163 428,163 402,213" fill="var(--pink-fold)"/>
    <rect x="374" y="104" width="346" height="59" fill="var(--brand-pink)"/>
  </svg>

  <div class="brand-name">BildeVOLD</div>

  <div class="holder-name">Henrik Audun Strandvik</div>
  <div class="holder-role">Dagligleder og Fotograf</div>

  <ul class="contact-list">
    <li class="contact-item" style="top:255px">555 264 0851
      <svg viewBox="0 0 30 30"><circle cx="15" cy="15" r="14" fill="#fff"/>
        <path d="M10.5 8.5c.8-.6 1.6-.4 2 .3l1.3 2.3c.3.6.2 1.2-.3 1.6l-1 .8c.7 1.7 2 3 3.7 3.8l.8-1c.4-.5 1-.6 1.6-.3l2.3 1.3c.7.4.9 1.3.3 2-1 1.2-2.3 1.7-3.8 1.2-3.9-1.3-6.9-4.3-8.1-8.2-.4-1.5 0-2.8 1.2-3.8z" fill="var(--brand-blue)"/></svg>
    </li>
    <li class="contact-item" style="top:300px">www.bildevold.example
      <svg viewBox="0 0 30 30"><circle cx="15" cy="15" r="14" fill="#fff"/>
        <circle cx="15" cy="15" r="8.5" fill="none" stroke="var(--brand-blue)" stroke-width="2"/>
        <ellipse cx="15" cy="15" rx="3.6" ry="8.5" fill="none" stroke="var(--brand-blue)" stroke-width="1.8"/>
        <line x1="6.5" y1="15" x2="23.5" y2="15" stroke="var(--brand-blue)" stroke-width="1.8"/></svg>
    </li>
    <li class="contact-item" style="top:342px">post@bildevold.example
      <svg viewBox="0 0 30 30"><circle cx="15" cy="15" r="14" fill="#fff"/>
        <rect x="8.5" y="10" width="13" height="10" rx="1" fill="none" stroke="var(--brand-blue)" stroke-width="1.8"/>
        <polyline points="8.8,10.5 15,15.5 21.2,10.5" fill="none" stroke="var(--brand-blue)" stroke-width="1.8"/></svg>
    </li>
    <li class="contact-item" style="top:388px">Kvernbakken9, 6040 Solvikvåg
      <svg viewBox="0 0 30 30"><circle cx="15" cy="15" r="14" fill="#fff"/>
        <path d="M15 7.5c-3.2 0-5.5 2.4-5.5 5.4 0 3.9 5.5 9.6 5.5 9.6s5.5-5.7 5.5-9.6c0-3-2.3-5.4-5.5-5.4z" fill="var(--brand-blue)"/>
        <circle cx="15" cy="12.9" r="2" fill="#fff"/></svg>
    </li>
  </ul>
</section>

<section class="card card--back" aria-label="Visittkort bakside">
  <div class="back-brand">BildeVOLD</div>
  <div class="social-row">
    <div class="social-item"><span class="social-dot"></span>BildeVOLD</div>
    <div class="social-item"><span class="social-dot"></span>BildeVOLD</div>
  </div>
</section>

</body>
</html>
```